Lotstallmart.com Webpage Design

Design Brief for lotstallmart.com (Copy of Brief also in attached Word file)

Name of Website- lotstallmart.com (existing logo and look & feel of website to be changed)

Logo - Finalised. The logo files are attached with the brief as “logo.jpeg”. The “Blue- Grey” version of the logo is for use on lighter backgrounds and the “Orange-White” version of the logo is for use on darker backgrounds. (A full Black version of the logo is also attached). Both versions may be used in different parts of the website. All attached files are in .png format.
Status - The website in functional and is undergoing user trials. However, we want to improve the look & feel of the website so at it seems
a. cotemporary,
b. Easy to Navigate
c. professional and
d. Vibrant.

Please visit ‘lotstallmart.com’ to check out the website and its functionalities – please use it only as a reference for the features & functions to be provided, however the designer should use a ‘Free Hand’ in designing the composition of various parts of the webpage without getting too influenced by the existing design

Objective of the Website ‘lotstallmart.com –
a. It is a portal focussed on listing of ‘Retail’ specific real-estate properties by developers, owners and realty brokers. The properties shall listed under the following four categories-
i. Retail Malls
ii. Shopping Complexes
iii. High-street shops
iv. Retail Warehouses
*refer lotstallmart.com for better clarity

b. The abovementioned properties shall be listed either for ‘Sale’ or ‘rent\lease’ or both

c. Users shall visit the site in case they wish to acquire a retail \ shop space either on ‘sale’ or ‘rent’. These Users would be able to specify the ‘Search Criteria’ through the tool-bars provided on the website – the ‘Search Criteria’ shall comprise of ‘Type of space category’, ‘City’, ‘Locality’, transaction type ie ‘Rent \ Sale’ and ‘Area Range’

d. The main revenue model for the website shall be listing fee ( or advertising charges ) payable by those listing their properties on the website.

Three Main Pages of Website (lotstallmart.com) that need to be designed -
a. Main Home Page (visit the web link - http://lotstallmart.com/ ) - The main home page has the “Search Toolbar” for specifying of Search Criteria by the User. It shall also have the following features & functions-
i. Main Advertising Banner
ii. Featured Projects
iii. New Launches
iv. Toolbar with buttons – ‘Advertise with Us’, ‘Listings Alert’, ‘Mart Wizards’, ‘Advertiser Login’

b. Property Listings Page (visit the web link - http://lotstallmart.com/gurgaon-in-india ) - The List of property options that match the Criteria specified by the ‘User’ get displayed on this page.

c. Property Detail Page - When the ‘User’ clicks on the “More….” Button on the ‘Property Listings Page’ (given in point b. above) the web page with the details of the property opens. (For Example – visit the web link - http://lotstallmart.com/vorne-Shopping-Complex-vorne-quadrion-gurgaon-636 )

Note:- Please refer to attached ‘Shopping’ related images the designer may use them on the website to provide a look & feel of retail if required – either separately or rotate in a single window

Target Market(s)

Retailers & Investors looking for retail space, Real Estate Brokers, Developers

Industry/Entity Type

Advertising

Number of Pages Required

3 page

Requirements
Must have
• Refer to existing site lotstallmart.com -- all the existing functionalities are a must have.
Nice to have
• The Designer may use the retail related images on the website if required for making it more vibrant. Refer attached images Shopping(1-6).jpg

```html
<!DOCTYPE html>
<html lang="en">
<head>
<meta charset="utf-8">
<title>Lotstallmart.com – Retail Space Portal</title>
<link href="https://fonts.googleapis.com/css2?family=Open+Sans:wght@300;400;600&family=Arimo:wght@400;700&display=swap" rel="stylesheet">
<style>
:root{
  --blue:#0aa0f5;
  --blue-dark:#0b8fe0;
  --blue-text:#1a8fd6;
  --grey-bg:#f2f2f2;
  --panel:#e4e4e4;
  --text:#444;
  --muted:#777;
  --footer:#3b3b3b;
  --footer-dark:#2f2f2f;
  --white:#fff;
}
*{box-sizing:border-box;margin:0;padding:0}
html,body{width:1200px;height:2177px;overflow:hidden;background:#fff}
body{font-family:"Arimo",Arial,sans-serif;color:var(--text);position:relative}
.wrap{position:absolute;left:98px;width:1003px}
.city-bar{top:0;height:40px;background:var(--blue);color:#fff;font-size:17px;display:flex;align-items:center;justify-content:center;letter-spacing:.2px}
.site-header{top:40px;height:123px;background:var(--grey-bg)}
.brand{position:absolute;left:24px;top:44px;display:flex;align-items:center;gap:10px}
.brand-dot{width:30px;height:30px;border-radius:50%;background:#3d4a5c}
.brand-name{font-family:"Open Sans",sans-serif;font-weight:600;font-size:25px;color:var(--blue)}
.nav-item{position:absolute;top:52px;width:180px;margin-left:-90px;text-align:center;font-size:15px;color:#555}
.nav-item small{display:block;font-size:12px;color:#777}
.account{position:absolute;left:813px;top:20px;width:176px;text-align:center;font-size:14px;color:#555;white-space:nowrap}
.login-btn{display:flex;align-items:center;justify-content:center;gap:16px;width:176px;height:42px;background:var(--blue);color:#fff;font-size:16px;margin:6px 0}
.search-panel{position:absolute;top:163px;left:98px;width:283px;height:514px;background:var(--panel);font-size:12px;color:#555}
.search-panel > *{position:absolute;left:17px;width:249px}
.fmt{top:17px;font-size:11.5px;white-space:nowrap}
.fmt a{color:var(--blue);text-decoration:underline}
.radios{top:60px;display:grid;grid-template-columns:1fr 1fr;row-gap:18px}
.radios span{display:flex;align-items:center;gap:8px;font-size:11.5px}
.radios i{width:10px;height:10px;border-radius:50%;background:#fff;border:1px solid #ccc}
.field-label{text-align:center}
.select{height:29px;background:#fff;display:flex;align-items:center;justify-content:space-between;padding-left:12px;font-size:11.5px}
.select b{width:27px;height:29px;border-left:1px solid #ddd;display:flex;align-items:center;justify-content:center}
.input{height:29px;background:#fff}
.search-btn{left:60px!important;width:176px!important;height:42px;background:var(--blue);color:#fff;font-size:16px;text-align:center;line-height:42px}
.hero{position:absolute;top:163px;left:381px;width:720px;height:514px}
.hero-photo{height:459px;background:linear-gradient(120deg,#d9c8a6 0%,#efe4cf 35%,#f08a2a 55%,#e8d9bd 75%,#b8a27c 100%)}
.dots{position:absolute;top:437px;left:50%;display:flex;gap:5px;transform:translateX(-50%)}
.dots i{width:7px;height:7px;border-radius:50%;background:#fff}
.dots i:last-child{background:var(--blue)}
.hero-tabs{height:55px;background:var(--blue);display:flex;color:#fff;text-align:center}
.hero-tabs div{flex:1;display:flex;flex-direction:column;justify-content:center;font-size:16px;border-right:1px solid rgba(255,255,255,.6);margin:7px 0}
.hero-tabs div:last-child{border:0}
.hero-tabs small{font-size:11.5px}
.section-title{position:absolute;left:98px;width:1003px;text-align:center;font-family:"Open Sans",sans-serif;font-weight:400;font-size:25px;color:#333;letter-spacing:.5px}
.section-title .sub{display:flex;align-items:center;justify-content:center;gap:10px;font-size:17px;color:var(--blue);margin-top:6px}
.section-title .sub i{width:130px;border-top:2px dotted #888}
.section-title .arrow{position:absolute;right:14px;top:18px}
.cards{position:absolute;left:98px;width:1003px;display:flex;gap:7px}
.card{width:195px;height:239px;background:#fff;box-shadow:0 5px 5px -3px rgba(0,0,0,.35);border:1px solid #eee;text-align:center;position:relative}
.card-photo{height:116px;margin:3px}
.card-tag{position:absolute;top:3px;left:3px;background:var(--blue);color:#fff;font-size:11.5px;padding:2px 10px}
.card h3{font-weight:400;font-size:14.5px;color:var(--blue-text);margin-top:10px;white-space:nowrap}
.card .loc{font-size:12px;color:var(--blue-text);margin-top:3px}
.card .cat{font-size:11px;color:#666;margin-top:3px}
.card .view{font-size:11.5px;color:#555;margin-top:17px}
.promo{position:absolute;top:1441px;left:98px;width:1003px;display:flex;gap:15px}
.promo-box{width:324px;height:330px;background:linear-gradient(135deg,var(--blue-dark),var(--blue) 50%,#1aa8f7);color:#fff;text-align:center;padding:24px 30px 0}
.promo-box h2{font-family:"Open Sans",sans-serif;font-weight:400;font-size:24px;margin-bottom:10px}
.promo-box p{font-size:11px;line-height:17px}
.promo-box .in{height:28px;background:#fff;color:#aaa;font-size:11.5px;text-align:left;padding:7px 9px;margin-top:20px;display:flex;justify-content:space-between}
.promo-box .in.tall{height:64px}
.promo-box .note{font-size:10.5px;text-align:left;margin-top:2px}
.promo-box .btn{display:block;width:156px;height:29px;background:#fff;color:var(--blue);font-size:15px;line-height:29px;margin:0 auto}
.site-footer{position:absolute;top:1806px;left:96px;width:1005px;height:370px;background:var(--footer);color:#ddd}
.footer-cols{display:flex;height:319px;padding-top:28px}
.footer-col{flex:1;padding:0 30px;border-right:2px solid #777;margin-bottom:28px}
.footer-col:last-child{border:0}
.footer-col h4{font-family:"Open Sans",sans-serif;font-weight:600;font-size:17px;margin:10px 0 36px;text-align:center}
.footer-col ul{list-style:none;font-size:10.5px;line-height:20px;columns:2}
.footer-col ul li::before{content:"• "}
.footer-col p{font-size:10.5px;line-height:20.5px;text-align:justify}
.socials{display:flex;justify-content:center;gap:6px;margin-top:16px}
.socials i{width:24px;height:24px;border-radius:50%;background:#fff}
.copyright{height:51px;background:var(--footer-dark);text-align:center;font-size:10.5px;line-height:51px}
</style>
</head>
<body>

<div class="wrap city-bar">Bangalore | Chennai | Greater Noida | Gurgaon | Hyderabad | Jaipur | Khanna | Kolkatta | Mumbai | Noida | Pune | Surat</div>

<header class="wrap site-header">
  <div class="brand"><span class="brand-dot"></span><span class="brand-name">lotstallmart.com</span></div>
  <div class="nav-item" style="left:383px">Advertise with us<small>Standard listing - FREE</small></div>
  <div class="nav-item" style="left:563px">Mart Wizards<small>Shop Search Services</small></div>
  <div class="nav-item" style="left:718px">Listing Alert</div>
  <div class="account">List Your Property Here
    <div class="login-btn">Advertiser Login <svg width="14" height="16"><path d="M0 0L14 8 0 16z" fill="#fff"/></svg></div>
    New Advertiser - Register</div>
</header>

<aside class="search-panel">
  <div class="fmt">Select Retail Format: <a>Meaning of Retail Format</a></div>
  <div class="radios">
    <span><i></i>Retail Malls</span><span><i></i>Shopping Complex</span>
    <span><i></i>High Street Shops</span><span><i></i>Retail Warehouses</span>
  </div>
  <div class="field-label" style="top:153px">Sale Or Rent Or Both:</div>
  <div class="select" style="top:175px">Both<b><svg width="10" height="7"><path d="M0 0h10L5 7z" fill="#aaa"/></svg></b></div>
  <div class="field-label" style="top:219px">Select City:</div>
  <div class="select" style="top:238px">-Select-<b><svg width="10" height="7"><path d="M0 0h10L5 7z" fill="#aaa"/></svg></b></div>
  <div class="field-label" style="top:283px">Select Locality/Micro-Market:</div>
  <div class="select" style="top:303px">-Select-<b><svg width="10" height="7"><path d="M0 0h10L5 7z" fill="#aaa"/></svg></b></div>
  <div class="field-label" style="top:380px">Enter Keywords:</div>
  <div class="input" style="top:400px"></div>
  <div class="search-btn" style="top:456px">SEARCH</div>
</aside>

<section class="hero">
  <div class="hero-photo" role="img" aria-label="Banner photo: shopper with colourful shopping bags in a bright mall atrium"></div>
  <div class="dots"><i></i><i></i><i></i></div>
  <div class="hero-tabs">
    <div>Retail Malls<small>Centrally Air-Conditioned</small></div>
    <div>Shopping Complex<small>Non Air-Conditioned Building</small></div>
    <div>High Street Shops<small>Road Facing Retail</small></div>
    <div>Retail Warehouses<small>Back-end Retail Storage</small></div>
  </div>
</section>

<div class="section-title" style="top:710px">FEATURED RETAIL PROJECTS
  <div class="sub"><i></i>Across India<i></i></div>
  <svg class="arrow" width="16" height="18"><path d="M0 0L16 9 0 18z" fill="#0aa0f5"/></svg>
</div>

<div class="cards" style="top:796px">
  <div class="card"><div class="card-photo" role="img" aria-label="Photo of mall building" style="background:linear-gradient(#b9cbe0,#8aa07a)"></div><span class="card-tag">Surat</span><h3>Verdant Plaza</h3><div class="loc">Althan</div><div class="cat">Shopping Complex</div><div class="view">View the listing</div></div>
  <div class="card"><div class="card-photo" role="img" aria-label="Photo of high street building at night" style="background:linear-gradient(#3a4a6a,#8a7a6a)"></div><span class="card-tag">Faridabad</span><h3>Arcadia 81 High Street</h3><div class="loc">Sector-81</div><div class="cat">Shopping Complex</div><div class="view">View the listing</div></div>
  <div class="card"><div class="card-photo" role="img" aria-label="Photo of commercial complex" style="background:linear-gradient(#9fc6e6,#c9d6de)"></div><span class="card-tag">Gurgaon</span><h3>Meridian Cosmo</h3><div class="loc">Sector-65</div><div class="cat">Shopping Complex</div><div class="view">View the listing</div></div>
  <div class="card"><div class="card-photo" role="img" aria-label="Photo of tower at dusk" style="background:linear-gradient(#1e3a7a,#c49a5a)"></div><span class="card-tag">Gurgaon</span><h3>Orbis 24K</h3><div class="loc">Sohna Road</div><div class="cat">Retail Malls</div><div class="view">View the listing</div></div>
  <div class="card"><div class="card-photo" role="img" aria-label="Photo of mall facade" style="background:linear-gradient(#c9ced6,#8a8d92)"></div><span class="card-tag">New Delhi</span><h3>Harbor Mall-Tagore Garden</h3><div class="loc">Tagore Garden</div><div class="cat">Retail Malls</div><div class="view">View the listing</div></div>
</div>

<div class="section-title" style="top:1070px">FEATURED NEW LAUNCHES
  <div class="sub"><i></i>Across India<i></i></div>
  <svg class="arrow" width="16" height="18"><path d="M0 0L16 9 0 18z" fill="#0aa0f5"/></svg>
</div>

<div class="cards" style="top:1154px">
  <div class="card"><div class="card-photo" role="img" aria-label="Rendering of retail development" style="background:linear-gradient(#d8d2c6,#a88a6e)"></div><span class="card-tag">Bhopal</span><h3>The Grand Bazaar Place</h3><div class="loc">Kolar Road</div><div class="cat">Retail Malls</div><div class="view">View the listing</div></div>
  <div class="card"><div class="card-photo" role="img" aria-label="Rendering of glass tower" style="background:linear-gradient(#2a4a8a,#8aa0c0)"></div><span class="card-tag">Noida</span><h3>Crest One</h3><div class="loc">Sector-18</div><div class="cat">Retail Malls</div><div class="view">View the listing</div></div>
  <div class="card"><div class="card-photo" role="img" aria-label="Rendering of shop row" style="background:linear-gradient(#7ab0e0,#c8b8a0)"></div><span class="card-tag">Mohali</span><h3>Town Core - SCO In Sector</h3><div class="loc">Sihon Majra</div><div class="cat">Shopping Complex</div><div class="view">View the listing</div></div>
  <div class="card"><div class="card-photo" role="img" aria-label="Rendering of shop row" style="background:linear-gradient(#7ab0e0,#c8b8a0)"></div><span class="card-tag">Mohali</span><h3>SCO In Sector 127 On</h3><div class="loc">Sihon Majra</div><div class="cat">Shopping Complex</div><div class="view">View the listing</div></div>
  <div class="card"><div class="card-photo" role="img" aria-label="Rendering of commercial street" style="background:linear-gradient(#c8d4e0,#b0807a)"></div><span class="card-tag">Gurgaon</span><h3>The Opal Sector 49</h3><div class="loc">Sector 102</div><div class="cat">Shopping Complex</div><div class="view">View the listing</div></div>
</div>

<section class="promo">
  <div class="promo-box">
    <h2>Listing Alert</h2>
    <p>Suscribe for Fortnightly Email update on<br>New Listings @ Lotstallmart.com</p>
    <div class="in">Enter your email address</div>
    <div class="in" style="margin-top:10px">Select options<span>⇕</span></div>
    <div class="note">(select retail format of interest)</div>
    <div class="in" style="margin-top:6px">Adilabad<span>▾</span></div>
    <div class="note">(select cities of interest)</div>
    <span class="btn" style="margin-top:20px">Subscribe</span>
  </div>
  <div class="promo-box">
    <h2>Editor's Choice</h2>
    <p>A "Select" Listing of Retail Properties Handpicked by our Editors based on their own positive evaluation on parameters &amp; attributes such as Design Concept, Location, Developer, Success Potential.<br>So Read On to Check Out for yourself ...............</p>
    <span class="btn" style="margin-top:132px">more...</span>
  </div>
  <div class="promo-box">
    <h2>Mart Wizards</h2>
    <p>Post your Retail Space requirement with us and our experts shall get back with suitable options and even help you in your transaction. This is a Free Service!</p>
    <div class="in" style="margin-top:14px">Enter your email address</div>
    <div class="in" style="margin-top:10px">Mobile</div>
    <div class="in tall" style="margin-top:10px">Add Description of Requirement</div>
    <span class="btn" style="margin-top:10px">Send</span>
  </div>
</section>

<footer class="site-footer">
  <div class="footer-cols">
    <div class="footer-col">
      <h4>About Retail Nexus</h4>
      <ul><li>About Us</li><li>Privacy Policy</li><li>Terms of Use</li><li>Contact Us</li><li>Site Map</li><li>Retail Malls</li><li>Shopping Complex</li><li>High Street Shops</li><li>Retail Warehouses</li></ul>
    </div>
    <div class="footer-col">
      <h4>www.lotstallmart.com</h4>
      <p>Lotstallmart.com - About Us Lotstallmart.com is a Specialised Web based platform for Retail Space, featuring properties across India under various formats such as Retail Malls, Shopping Complexes, High-street Shops. Also featured are Retail Warehouses which provide the logistic back-end for the retail business. Lotstallmart.com is useful to various category of users as follows- a. Devel More...</p>
      <div class="socials"><i></i><i></i><i></i><i></i><i></i></div>
    </div>
    <div class="footer-col">
      <h4>Contact</h4>
      <p style="text-align:left">Retail Nexus<br>Unit 406, 4th Floor,<br>Lorem Ipsum is simply,<br>Sector-x, Gurgaon - 122002<br><br>Phone : 000-000-0000<br>Fax : 000 - 000 - 000</p>
    </div>
  </div>
  <div class="copyright">Copyright © 2013 Retail Nexus.com. All rights reserved.</div>
</footer>

</body>
</html>
```